Redesign a Start-Up Dating Website

Website: https://morvelique.com.
Make sure the design has an island style theme.
I would like the 7 pages of my website to have a new and professional look. I want the same colors to remain, but I want a creative look for all the pages. This is a dating website that is in the startup stage. So, I want to give my entire website a custom makeover. I want something that will stand out from the other dating sites. Something that will attract more people to want to use my services, and hopefully get new members.
Target Market(s)
Dating
Industry/Entity Type
Dating
Coding
Coded - Design and coding required
Number of Pages Required
5+ page
Font styles to use
Other font styles liked:
- Decorative, San Serif
Requirements
Must have
- The design must have the original colors and a stylish font to go along. The design must be creative, welcoming, and professional. I would like an island style theme for the website. This is a dating website so make sure that the design is tailored to that aspect.
Nice to have
- It would be nice to have a decorative font and a professional style on all the pages. Make sure the design will be mobile responsive and friendly for all the pages on the website.
Should not have
- The design should not be bland and uncreative.

```html
<!DOCTYPE html>
<html lang="en">
<head>
<meta charset="utf-8">
<title>Morvelique – Island Dating</title>
<link rel="stylesheet" href="https://fonts.googleapis.com/css2?family=Courgette&family=Open+Sans:wght@400;600;700&display=swap">
<style>
:root{
  --sea-deep:#0f6f9e;
  --sea:#2a9fcf;
  --sea-light:#7fd0ea;
  --header:#1c86bd;
  --orange:#f39320;
  --green:#2db493;
  --purple:#6b3a9b;
  --ink:#3b3b3b;
  --muted:#6d6d6d;
  --title-green:#2f7a2b;
  --footer:#16263f;
  --footer-dark:#0e1a2e;
  --white:#ffffff;
  --sand:#e9c79a;
  --skin:#c98b6b;
}
*{box-sizing:border-box;margin:0;padding:0}
html,body{width:1200px;height:2396px;overflow:hidden}
body{
  font-family:"Open Sans",sans-serif;color:var(--ink);position:relative;
  background:linear-gradient(180deg,var(--sea-light) 0%,var(--sea) 30%,#58b9dc 50%,var(--sea-deep) 65%,var(--sea) 85%,var(--sea-deep) 100%);
}
.abs{position:absolute}
/* header */
.topbar{left:0;top:0;width:1200px;height:40px;background:var(--header)}
.topbar .account{position:absolute;right:0;top:0;height:40px;width:330px;background:var(--orange);
  display:flex;gap:40px;align-items:center;justify-content:center;color:var(--white);font-size:15px;font-weight:600;
  clip-path:polygon(30px 0,100% 0,100% 100%,0 100%)}
.mainbar{left:0;top:40px;width:1200px;height:72px;background:var(--header)}
.brand{position:absolute;left:80px;top:12px;display:flex;align-items:center;gap:12px}
.brand .dot{width:44px;height:44px;border-radius:50%;background:var(--orange)}
.brand span{font-weight:700;font-size:34px;color:var(--white)}
.nav{position:absolute;right:80px;top:0;height:72px;display:flex;gap:26px;align-items:center;list-style:none}
.nav li{color:var(--white);font-size:14px;font-weight:600;letter-spacing:.5px}
.nav li.current{color:var(--orange)}
/* hero */
.hero{left:80px;top:112px;width:1040px;height:500px;
  background:
    radial-gradient(ellipse 260px 300px at 640px 300px,rgba(214,150,115,.95),rgba(214,150,115,0) 70%),
    radial-gradient(ellipse 200px 140px at 560px 40px,rgba(60,110,60,.7),rgba(60,110,60,0) 70%),
    linear-gradient(180deg,#9fdcf0 0%,#5fbde0 25%,#2a9fcf 55%,#1b78aa 100%)}
.hero h1{position:absolute;left:70px;top:80px;font-family:"Courgette",cursive;font-weight:400;font-size:56px;color:var(--white);text-shadow:0 2px 6px rgba(0,0,0,.25)}
.hero p{position:absolute;left:70px;width:360px;font-size:17px;color:var(--white);text-shadow:0 1px 3px rgba(0,0,0,.3)}
.hero .btn{position:absolute;left:70px;top:310px;padding:12px 34px;border:2px solid var(--purple);border-radius:30px;
  color:var(--white);font-family:"Courgette",cursive;font-size:20px;background:rgba(255,255,255,.15)}
.arrow{position:absolute;top:225px;width:34px;height:50px;background:var(--orange);display:flex;align-items:center;justify-content:center}
/* features */
.feature{top:650px;width:330px;height:230px;color:var(--white);text-align:center;padding:80px 30px 0}
.feature h3{font-family:"Courgette",cursive;font-weight:400;font-size:24px;margin-bottom:10px}
.feature p{font-size:13px;line-height:1.5}
.badge{position:absolute;top:-50px;left:115px;width:100px;height:100px;border-radius:50%;border:5px solid var(--white);
  display:flex;align-items:center;justify-content:center}
.f-green{left:80px;background:var(--green)} .f-green .badge{background:var(--green)}
.f-purple{left:435px;background:var(--purple)} .f-purple .badge{background:var(--purple)}
.f-orange{left:790px;background:var(--orange)} .f-orange .badge{background:var(--orange)}
/* welcome */
.welcome{left:80px;top:910px;width:1040px;height:300px;background:rgba(255,255,255,.6)}
.section-title{font-family:"Courgette",cursive;font-weight:400;color:var(--title-green);font-size:38px}
.welcome .section-title{position:absolute;left:30px;top:30px}
.welcome p{position:absolute;left:30px;top:95px;width:640px;font-size:15px;line-height:1.65;color:var(--ink)}
.welcome .btn{position:absolute;left:30px;top:226px;padding:10px 26px;border:3px solid var(--purple);border-radius:30px;
  color:var(--purple);font-weight:700;font-size:15px;background:var(--white)}
.welcome-photo{left:770px;top:880px;width:330px;height:340px;
  background:
    radial-gradient(ellipse 120px 160px at 180px 150px,rgba(201,139,107,.95),rgba(201,139,107,0) 70%),
    radial-gradient(ellipse 130px 110px at 150px 300px,rgba(236,130,165,.95),rgba(236,130,165,0) 75%),
    linear-gradient(180deg,#8ccbe4 0%,#b9dde9 45%,#e7d2b4 100%)}
/* community */
.community-band{left:80px;top:1226px;width:1040px;height:84px;background:rgba(255,255,255,.72)}
.community-title{left:0;top:1245px;width:1200px;text-align:center}
.community{left:80px;top:1310px;width:1040px;height:250px;background:var(--white);
  display:flex;justify-content:space-around;align-items:center;padding:0 30px}
.member{width:160px;height:160px;border-radius:50%;border:6px solid var(--sea-light);position:relative}
.member .label{position:absolute;left:0;right:0;top:62px;text-align:center;color:var(--white);font-weight:700;font-size:15px}
/* benefits */
.benefits-title{left:0;top:1660px;width:1200px;text-align:center;color:var(--white)}
.benefits-sub{left:0;top:1722px;width:1200px;text-align:center;color:var(--white);font-style:italic;font-size:18px}
.signup{left:0;top:1770px;width:1200px;display:flex;justify-content:center;gap:14px}
.signup .field{width:300px;height:52px;background:var(--white);border-radius:4px;padding:15px 16px;font-size:15px;color:var(--muted)}
.signup .btn{margin-left:40px;width:150px;height:52px;border:3px solid var(--purple);border-radius:30px;background:var(--white);
  color:var(--purple);font-weight:700;font-size:16px;display:flex;align-items:center;justify-content:center}
/* gallery */
.gallery{left:80px;top:1885px;width:1040px;height:155px;display:flex;gap:4px}
.gallery div{flex:1;background:
  radial-gradient(ellipse 50px 60px at 50% 60%,rgba(201,139,107,.9),rgba(201,139,107,0) 75%),
  linear-gradient(180deg,#a8dcef 0%,#6fbfdd 45%,#e9c79a 100%)}
.gallery div:nth-child(even){background:
  radial-gradient(ellipse 50px 60px at 50% 55%,rgba(180,110,85,.9),rgba(180,110,85,0) 75%),
  linear-gradient(180deg,#f4cf8e 0%,#e69f63 50%,#4b87a8 100%)}
/* footer */
.footer{left:0;top:2060px;width:1200px;height:300px;background:var(--footer);color:var(--white)}
.footer h4{font-size:15px;font-weight:700;margin-bottom:18px}
.col{position:absolute;top:40px}
.sitemap{list-style:none}
.sitemap li{font-size:14px;line-height:27px;display:flex;align-items:center;gap:10px}
.sitemap li::before{content:"";width:7px;height:7px;background:var(--orange)}
.row{display:flex;align-items:center;gap:12px;font-size:14px;margin-bottom:18px}
.ico{width:32px;height:32px;border-radius:50%;background:#2b4166;display:flex;align-items:center;justify-content:center}
.f-brand{left:880px;width:240px}
.f-brand .brand{position:static;margin-bottom:14px}
.f-brand .brand span{font-size:30px}
.f-brand p{font-size:13px;line-height:1.6;color:#c9d3e3}
.copyright{left:0;top:2360px;width:1200px;height:36px;background:var(--footer-dark);color:#c9d3e3;font-size:13px;
  display:flex;align-items:center;justify-content:center}
</style>
</head>
<body>

<div class="abs topbar"><div class="account"><span>Login</span><span>Register</span></div></div>
<div class="abs mainbar">
  <div class="brand"><div class="dot"></div><span>Morvelique</span></div>
  <ul class="nav">
    <li class="current">HOME</li><li>SEARCH</li><li>MEMBERS</li><li>EXTRAS</li><li>ABOUT</li><li>PREMIUM</li><li>CONTACT</li>
  </ul>
</div>

<section class="abs hero" role="img" aria-label="Couple embracing in tropical sea water under a palm-lined sky">
  <h1>Choose your soul mate</h1>
  <p style="top:170px">Find your perfect island love today</p>
  <p style="top:200px">Create, connect and start your journey</p>
  <p style="top:230px">Meet singles who share your dreams</p>
  <div class="btn">Join Us Free</div>
  <div class="arrow" style="left:0"><svg width="14" height="20"><path d="M12 2 3 10l9 8" fill="none" stroke="#fff" stroke-width="3"/></svg></div>
  <div class="arrow" style="right:0"><svg width="14" height="20"><path d="M2 2l9 8-9 8" fill="none" stroke="#fff" stroke-width="3"/></svg></div>
</section>

<div class="abs feature f-green">
  <div class="badge"><svg width="50" height="50" viewBox="0 0 50 50" fill="none" stroke="#fff" stroke-width="3"><rect x="8" y="6" width="34" height="38" rx="4"/><circle cx="25" cy="20" r="6"/><path d="M15 38c2-7 18-7 20 0"/></svg></div>
  <h3>Create a Profile</h3>
  <p>Let people know all about you: upload photos, share your interests and tell everyone what makes your heart beat a little faster.</p>
</div>
<div class="abs feature f-purple">
  <div class="badge"><svg width="56" height="50" viewBox="0 0 56 50" fill="none" stroke="#fff" stroke-width="3"><circle cx="18" cy="18" r="7"/><circle cx="38" cy="18" r="7"/><path d="M6 42c2-10 22-10 24 0M26 42c2-10 22-10 24 0"/></svg></div>
  <h3>Find Matches</h3>
  <p>Browse other users and feel the excitement of getting your first message and getting to know potential dates in a safe and fun environment.</p>
</div>
<div class="abs feature f-orange">
  <div class="badge"><svg width="56" height="50" viewBox="0 0 56 50" fill="none" stroke="#fff" stroke-width="3"><circle cx="16" cy="12" r="6"/><circle cx="40" cy="12" r="6"/><path d="M8 44V26h16v18M32 44V26h16v18M25 20l3 4 3-4"/></svg></div>
  <h3>Start Dating</h3>
  <p>Once you've found your potential partners, it's time to meet up and finally start the island romance of your dreams together.</p>
</div>

<section class="abs welcome">
  <h2 class="section-title">Welcome To Morvelique</h2>
  <p>Morvelique aims to provide a straightforward, easy-to-use online dating service. We don't want complicated things to reduce the amount of people you are able to talk to. Everyone deserves a fair chance, and we believe that every person you meet could be the one. Join our island community and find someone worth the journey on the dating site you can trust.</p>
  <div class="btn">LEARN MORE</div>
</section>
<div class="abs welcome-photo" role="img" aria-label="Smiling couple embracing on a tropical beach"></div>

<div class="abs community-band"></div>
<h2 class="abs section-title community-title">Join This Community Of Morvelique Members</h2>
<section class="abs community">
  <div class="member" role="img" aria-label="Member photo" style="background:radial-gradient(circle at 50% 40%,#8a62b0,#5a3482)"><div class="label">ILL, Germany</div></div>
  <div class="member" role="img" aria-label="Member photo" style="background:radial-gradient(circle at 50% 45%,#d2a184,#8a5c44)"></div>
  <div class="member" role="img" aria-label="Member photo" style="background:radial-gradient(circle at 50% 45%,#9a6e56,#4e3328)"></div>
  <div class="member" role="img" aria-label="Member photo" style="background:radial-gradient(circle at 50% 45%,#e0bda5,#9f7b64)"></div>
  <div class="member" role="img" aria-label="Member photo" style="background:radial-gradient(circle at 50% 45%,#7fd0ea,#2a8fbf)"></div>
</section>

<h2 class="abs section-title benefits-title">Morvelique Benefits</h2>
<p class="abs benefits-sub">Affordable Easy Sign - Up And cancellation Processes</p>
<div class="abs signup">
  <div class="field">Enter Name *</div>
  <div class="field">Enter Email *</div>
  <div class="btn">SUBSCRIBE</div>
</div>

<div class="abs gallery" role="img" aria-label="Strip of photos showing happy couples on beaches">
  <div></div><div></div><div></div><div></div><div></div><div></div><div></div><div></div>
</div>

<footer class="abs footer">
  <div class="col" style="left:80px">
    <h4>SITEMAP</h4>
    <ul class="sitemap"><li>Home</li><li>Search</li><li>Members</li><li>Extras</li><li>About</li><li>Premium</li><li>Contact</li></ul>
  </div>
  <div class="col" style="left:340px">
    <h4>CONTACT US</h4>
    <div class="row"><div class="ico"><svg width="16" height="12"><rect x="1" y="1" width="14" height="10" fill="none" stroke="#fff"/><path d="M1 1l7 6 7-6" fill="none" stroke="#fff"/></svg></div>contact@morvelique.com</div>
    <div class="row"><div class="ico"><svg width="14" height="14"><circle cx="7" cy="7" r="5" fill="none" stroke="#fff"/></svg></div>Support Center</div>
  </div>
  <div class="col" style="left:600px">
    <h4>Follow Us</h4>
    <div class="row"><div class="ico"></div>Pagebook</div>
    <div class="row"><div class="ico"></div>Chirper</div>
    <div class="row"><div class="ico"></div>Linkworks</div>
  </div>
  <div class="col f-brand">
    <div class="brand"><div class="dot"></div><span>Morvelique</span></div>
    <p>Morvelique aims to provide a simple, friendly, easy-to-use online dating service, so nothing stands between you and the people you hope to meet on the island.</p>
  </div>
</footer>
<div class="abs copyright">© Morvelique - 2017 All rights reserved | Privacy Policy</div>

</body>
</html>
```